Photo booth placards - Customers select after a game for a fun group photo

i am wanting 24 photobooth placards to fit on a peice of corflute (2400 x 1220) all on one file to print. Must be Bright and fun, each one different style /colour.
Escape room placards- approx. A3(file size with all on the one file 2400 x 1220) Require as a source file and high res pdf.
1. Photo Booth - Grab a prop and strike a post (this one is for the box that will contain the other signs)
2. Photo Booth - Grab a prop and strike a post (this one is for the box that will contain the other signs)
3. GENIUS
4. Nailed it!
5. I’m Awesome
6. We escaped
7. (arrow left) They were no help (Arrow Right)
8. We did it!
9. I’m still confused??
10. They Should have listened to me
11. Weakest link (arrow)
12. I’m the smart one
13. Escape Artist
14. I did EVERYTHING
15. Winners
16. No one listens to me
17. I survived by my wits (and good looks)
18. Escaped in time - woohoo!
19. We ALMOST beat the clock
20. (arrow left) Genius – We Escaped- Sidekick (arrow right)
21. We suck
22. I’m glad they’re smart
23. Mission completed
24. I’m with stupid (arrow)

some sample ideas attached...

```html
<!DOCTYPE html>
<html lang="en">
<head>
<meta charset="utf-8">
<title>Escape Room Photo Booth Placards</title>
<link rel="stylesheet" href="https://fonts.googleapis.com/css2?family=Bebas+Neue&family=Federo&family=Dancing+Script:wght@600&family=Anton&family=Press+Start+2P&family=Playfair+Display:ital@1&family=Abril+Fatface&family=Cinzel:wght@600&display=swap">
<style>
  :root{
    --paper:#ffffff;
    --teal:#2ab8cb;
    --teal-light:#7dd4dc;
    --gold:#f2c21b;
    --pink:#f0218f;
    --sunny:#f0d838;
    --navy:#2d2554;
    --sky:#5aaac8;
    --jade:#0fb0a0;
    --black:#000000;
    --hazard:#ffc900;
    --night:#2a0e6a;
    --dusk:#7a1a8a;
    --ground:#1f2e38;
    --grape:#9b0a9c;
    --camera:#e8224f;
  }
  html,body{margin:0;padding:0;overflow:hidden;}
  body{width:1200px;height:1200px;background:var(--paper);position:relative;}
  .placard{position:absolute;width:515px;height:262px;overflow:hidden;}
  .col-left{left:70px;} .col-right{left:614px;}
  .row-1{top:184px;} .row-2{top:468px;} .row-3{top:754px;}

  /* Winners */
  .winners{background:var(--teal);}
  .winners__word{position:absolute;left:0;right:0;top:56px;text-align:center;font:142px/1 "Bebas Neue",sans-serif;color:var(--teal-light);letter-spacing:2px;}
  .winners__trophy{position:absolute;left:196px;top:52px;width:122px;height:177px;background:linear-gradient(var(--gold) 70%,var(--navy) 70%);border-radius:10px 10px 4px 4px;}

  /* Photo booth */
  .booth--sunny{background:var(--pink);}
  .booth--jade{background:var(--sky);}
  .booth__sticker{position:absolute;left:22px;top:12px;width:480px;height:240px;background:var(--paper);border-radius:34px;}
  .booth__panel{position:absolute;left:42px;top:40px;width:432px;height:192px;border-radius:18px;}
  .booth--sunny .booth__panel{background:var(--sunny);}
  .booth--jade .booth__panel{background:var(--jade);}
  .booth__tape{position:absolute;width:74px;height:9px;background:var(--navy);border-radius:5px;}
  .tape-tl{left:28px;top:42px;transform:rotate(-40deg);}
  .tape-tr{right:22px;top:44px;transform:rotate(40deg);}
  .tape-bl{left:28px;bottom:44px;transform:rotate(48deg);}
  .tape-br{right:22px;bottom:44px;transform:rotate(-40deg);}
  .booth__title{position:absolute;left:145px;top:76px;width:220px;font:62px/50px "Federo",sans-serif;color:var(--navy);margin:0;text-align:center;letter-spacing:-3px;white-space:nowrap;}
  .booth--jade .booth__title{color:var(--paper);-webkit-text-stroke:2px var(--navy);paint-order:stroke fill;}
  .booth__tagline{position:absolute;left:0;right:0;top:180px;text-align:center;font:600 29px/1 "Dancing Script",cursive;color:var(--navy);white-space:nowrap;}
  .booth__camera{position:absolute;width:54px;height:42px;background:var(--camera);border-radius:10px;border:3px solid var(--paper);}
  .cam-left{left:66px;top:134px;transform:rotate(-12deg);}
  .cam-right{left:374px;top:92px;transform:rotate(8deg);}

  /* Genius / sidekick */
  .escaped{background:var(--black);}
  .escaped__band{position:absolute;left:0;width:100%;height:36px;background:var(--hazard);}
  .band-top{top:0;} .band-bottom{bottom:0;}
  .escaped__label{position:absolute;top:104px;font:40px/1 "Anton",sans-serif;color:var(--paper);}
  .label-genius{left:70px;} .label-sidekick{left:326px;}
  .escaped__arrow{position:absolute;top:106px;}
  .arrow-left{left:8px;} .arrow-right{left:462px;}
  .escaped__badge{position:absolute;left:191px;top:66px;}
  .escaped__stamp{position:absolute;left:186px;top:98px;width:138px;text-align:center;font:29px/0.95 "Anton",sans-serif;color:var(--paper);transform:rotate(-8deg);}

  /* Mission */
  .mission{background:linear-gradient(var(--night) 0%,var(--dusk) 48%,var(--ground) 48%,var(--ground) 100%);}
  .mission__ground{position:absolute;left:0;bottom:0;width:100%;height:136px;background:linear-gradient(var(--ground),#24385a);}
  .mission__title{position:absolute;left:0;right:0;top:70px;text-align:center;margin:0;font:47px/60px "Press Start 2P",monospace;white-space:nowrap;background:linear-gradient(#ffffff 0%,#c9ccd6 45%,#6d7280 55%,#e8eaf0 100%);-webkit-background-clip:text;background-clip:text;color:transparent;}

  /* Survived */
  .survived{background:var(--pink);}
  .survived__blob{position:absolute;left:22px;top:26px;}
  .survived__text{position:absolute;left:0;right:0;text-align:center;color:var(--paper);white-space:nowrap;}
  .line-survived{top:50px;font:italic 50px/1 "Playfair Display",serif;}
  .line-wits{top:98px;font:64px/1 "Abril Fatface",serif;}
  .line-looks{top:174px;font:600 25px/1 "Cinzel",serif;letter-spacing:1.5px;}
</style>
</head>
<body>

<section class="placard winners col-left row-1">
  <div class="winners__word">WINNERS</div>
  <div class="winners__trophy" role="img" aria-label="Gold trophy illustration on a number one pedestal"></div>
</section>

<section class="placard booth--sunny col-right row-1">
  <div class="booth__sticker"></div>
  <div class="booth__panel"></div>
  <span class="booth__tape tape-tl"></span><span class="booth__tape tape-tr"></span>
  <span class="booth__tape tape-bl"></span><span class="booth__tape tape-br"></span>
  <div class="booth__camera cam-left" role="img" aria-label="Pink camera illustration"></div>
  <div class="booth__camera cam-right" role="img" aria-label="Pink camera illustration"></div>
  <h2 class="booth__title">PHOTO<br>BOOTH</h2>
  <div class="booth__tagline">Grab a prop and strike a post</div>
</section>

<section class="placard escaped col-left row-2">
  <div class="escaped__band band-top" role="img" aria-label="Yellow and black hazard stripe band"></div>
  <div class="escaped__band band-bottom" role="img" aria-label="Yellow and black hazard stripe band"></div>
  <svg class="escaped__arrow arrow-left" width="46" height="44" viewBox="0 0 46 44"><polygon points="0,22 22,0 22,13 46,13 46,31 22,31 22,44" fill="var(--hazard)"/></svg>
  <span class="escaped__label label-genius">GENIUS</span>
  <svg class="escaped__badge" width="130" height="130" viewBox="0 0 130 130"><circle cx="65" cy="65" r="62" fill="none" stroke="var(--hazard)" stroke-width="3"/><circle cx="65" cy="65" r="54" fill="none" stroke="var(--hazard)" stroke-width="7"/></svg>
  <div class="escaped__stamp">WE<br>ESCAPED</div>
  <span class="escaped__label label-sidekick">SIDEKICK</span>
  <svg class="escaped__arrow arrow-right" width="46" height="44" viewBox="0 0 46 44"><polygon points="46,22 24,0 24,13 0,13 0,31 24,31 24,44" fill="var(--hazard)"/></svg>
</section>

<section class="placard booth--jade col-right row-2">
  <div class="booth__sticker"></div>
  <div class="booth__panel"></div>
  <span class="booth__tape tape-tl"></span><span class="booth__tape tape-tr"></span>
  <span class="booth__tape tape-bl"></span><span class="booth__tape tape-br"></span>
  <div class="booth__camera cam-left" role="img" aria-label="Pink camera illustration"></div>
  <div class="booth__camera cam-right" role="img" aria-label="Pink camera illustration"></div>
  <h2 class="booth__title">PHOTO<br>BOOTH</h2>
  <div class="booth__tagline">Grab a prop and strike a post</div>
</section>

<section class="placard mission col-left row-3">
  <div class="mission__ground" role="img" aria-label="Retro neon grid landscape with dark mountains"></div>
  <h2 class="mission__title">MISSION<br>COMPLETED</h2>
</section>

<section class="placard survived col-right row-3">
  <svg class="survived__blob" width="470" height="220" viewBox="0 0 470 220"><path d="M60 30 C120 0 190 30 250 14 C320 -4 400 20 430 60 C470 100 460 160 420 190 C370 225 290 200 220 212 C150 224 70 210 30 170 C-10 130 0 60 60 30 Z" fill="var(--grape)"/></svg>
  <div class="survived__text line-survived">I survived</div>
  <div class="survived__text line-wits">by my wits</div>
  <div class="survived__text line-looks">(AND GOOD LOOKS)</div>
</section>

</body>
</html>
```